Belmont Ridge Business Card Design Project

We have recently rebranded and would like to design new business cards that incorporate the corporate logo - double sided cards with corporate logo on one side and contact details on the other

Target Market(s)

Sophisticated and high net worth investors and finance industry professionals

Industry/Entity Type

Funds Management

Contact Information for Business Card

The card should prominently feature the company name and logo. Other details will be standard contact details for each staff member - name, address, phone, email, website

Colors
0054AA
0677BA
7BADD7
CADEEF
E8F1F8

Requirements
Must have
• Double-sided design with one side prominently featuring the corporate logo and the other side with all standard contact details

```html
<!DOCTYPE html>
<html lang="en">
<head>
<meta charset="utf-8">
<title>Belmont Ridge – Business Card</title>
<link rel="stylesheet" href="https://fonts.googleapis.com/css2?family=Open+Sans:wght@400;600;700&display=swap">
<style>
  :root {
    --backdrop: #acacac;
    --card-dark: #0b111a;
    --card-light: #ffffff;
    --brand-navy: #1f4277;
    --name-blue: #6a9bcd;
    --ink: #111111;
    --muted: #6d6d6d;
    --white: #ffffff;
  }
  * { margin: 0; padding: 0; box-sizing: border-box; }
  html, body {
    width: 1200px; height: 1000px; overflow: hidden;
    background: var(--backdrop);
    font-family: "Open Sans", Arial, sans-serif;
  }
  .card {
    position: absolute; top: 338px;
    width: 514px; height: 296px;
    box-shadow: 0 18px 40px rgba(0,0,0,0.35);
  }
  .card--front { left: 57px; background: var(--card-dark); }
  .card--back { left: 614px; background: var(--card-light); }

  .wordmark {
    position: absolute; left: 0; right: 0;
    text-align: center;
    font-weight: 600;
    text-transform: uppercase;
    letter-spacing: 1.5px;
    white-space: nowrap;
  }
  .card--front .wordmark {
    top: 160px; font-size: 29px; color: var(--white);
  }
  .card--back .wordmark {
    left: 22px; right: auto; width: 220px;
    top: 158px; font-size: 22px; color: var(--brand-navy);
    letter-spacing: 1px;
  }

  .details { position: absolute; left: 256px; top: 80px; }
  .person-name {
    font-size: 14px; font-weight: 700; letter-spacing: 1.2px;
    color: var(--name-blue); text-transform: uppercase; line-height: 17px;
  }
  .person-role {
    font-size: 14px; font-weight: 700; letter-spacing: 1.2px;
    color: var(--ink); text-transform: uppercase; line-height: 17px;
  }
  .contact-list { list-style: none; color: var(--muted); font-size: 14px; line-height: 17px; }
  .contact-list--address { margin-top: 22px; }
  .contact-list--lines { margin-top: 17px; }
  .contact-item { position: relative; padding-left: 20px; }
  .contact-icon {
    position: absolute; left: 0; top: 4px;
    width: 11px; height: 11px; fill: var(--brand-navy);
  }
</style>
</head>
<body>
  <section class="card card--front" aria-label="Card front">
    <div class="wordmark">Belmont Ridge</div>
  </section>

  <section class="card card--back" aria-label="Card back">
    <div class="wordmark">Belmont Ridge</div>

    <div class="details">
      <p class="person-name">Daniel Whitcombe</p>
      <p class="person-role">Portfolio Manager</p>

      <ul class="contact-list contact-list--address">
        <li class="contact-item">
          <svg class="contact-icon" viewBox="0 0 12 12" aria-hidden="true"><path d="M6 0a4 4 0 0 0-4 4c0 3 4 8 4 8s4-5 4-8a4 4 0 0 0-4-4zm0 5.6A1.6 1.6 0 1 1 6 2.4a1.6 1.6 0 0 1 0 3.2z"/></svg>
          Level 14 Harbour House,<br>52 Kent Lane,<br>Sydney NSW 2000
        </li>
      </ul>

      <ul class="contact-list contact-list--lines">
        <li class="contact-item">
          <svg class="contact-icon" viewBox="0 0 12 12" aria-hidden="true"><path d="M2.4 0.6l2 2.2-1.1 1.4c.8 1.7 2 2.9 3.6 3.7l1.4-1.1 2.2 2-1 2.2C4.8 11 1 7.2 0.2 1.6z"/></svg>
          +02 9400 1736
        </li>
        <li class="contact-item">
          <svg class="contact-icon" viewBox="0 0 12 12" aria-hidden="true"><path d="M0.5 2.5h11v7h-11z" fill="none" stroke="#1f4277" stroke-width="1"/><path d="M0.5 2.5l5.5 4 5.5-4" fill="none" stroke="#1f4277" stroke-width="1"/></svg>
          enquiries@belmontridge.com
        </li>
        <li class="contact-item">
          <svg class="contact-icon" viewBox="0 0 12 12" aria-hidden="true"><circle cx="6" cy="6" r="5.3" fill="none" stroke="#1f4277" stroke-width="1.1"/><ellipse cx="6" cy="6" rx="2.2" ry="5.3" fill="none" stroke="#1f4277" stroke-width="1"/><path d="M0.8 6h10.4M1.6 3.4h8.8M1.6 8.6h8.8" stroke="#1f4277" stroke-width="0.9"/></svg>
          www.belmontridge.com
        </li>
      </ul>
    </div>
  </section>
</body>
</html>
```